Podcastcover
Zielgruppe
Wir sind eine KI Firma und möchten einen Podcast starten. Unsere Zielgruppe sind CEO´s, CTO`s, IT-Entscheider und Beratungsunternehmen. Hierzu benötigen wir ein cooles und ausfälliges Cover.
Der Name des Podcast ist : KI nullzweidrei
Aufgabenstellung
Hoher Wiedererkennungswert
Folgendes Bild soll mit auf das Cover

```html
<!DOCTYPE html>
<html lang="de">
<head>
<meta charset="utf-8">
<title>KI nullzweidrei – Podcastcover</title>
<link rel="stylesheet" href="https://fonts.googleapis.com/css2?family=Archivo:wdth,wght@125,900&display=swap">
<style>
  :root {
    --ink: #000000;
    --teal: #5abfbf;
    --teal-deep: #4fb3b3;
    --white: #ffffff;
    --steel-light: #d9d6d3;
    --steel-dark: #6f6a66;
  }
  html, body {
    margin: 0;
    padding: 0;
    width: 1200px;
    height: 1200px;
    overflow: hidden;
    background: var(--ink);
  }
  .cover {
    position: relative;
    width: 1200px;
    height: 1200px;
    overflow: hidden;
    background: var(--ink);
    font-family: "Archivo", "Arial Black", sans-serif;
    font-weight: 900;
    font-stretch: 125%;
  }
  .cover__band {
    position: absolute;
    inset: 0;
  }
  .cover__portrait {
    position: absolute;
    left: 571px;
    top: 366px;
  }
  .cover__photo {
    position: absolute;
    left: 101px;
    top: 52px;
    width: 320px;
    height: 224px;
    background: linear-gradient(100deg, var(--steel-dark) 0%, var(--steel-light) 55%, var(--white) 75%);
  }
  .brand {
    position: absolute;
    right: 94px;
    top: 74px;
    margin: 0;
    font-size: 104px;
    line-height: 1;
    color: var(--white);
    white-space: nowrap;
  }
  .title {
    position: absolute;
    left: 88px;
    top: 0;
    margin: 0;
    font-weight: 900;
  }
  .title__line {
    position: absolute;
    left: 0;
    display: block;
    font-size: 232px;
    line-height: 1;
    letter-spacing: -0.01em;
    white-space: nowrap;
    color: var(--white);
  }
  .title__line--ki { top: 286px; color: var(--teal); }
  .title__line--1 { top: 494px; }
  .title__line--2 { top: 702px; }
  .title__line--3 { top: 910px; }
</style>
</head>
<body>
<main class="cover">
  <svg class="cover__band" width="1200" height="1200" viewBox="0 0 1200 1200" aria-hidden="true">
    <polygon points="0,671 1200,311 1200,1200 0,1200" fill="var(--teal)"/>
  </svg>

  <svg class="cover__portrait" width="629" height="834" viewBox="0 0 629 834" role="img" aria-label="Karikatur eines grinsenden Mannes mit Halbglatze, schwarze Tuschezeichnung auf Türkis">
    <path d="M40 420 C40 180 200 0 420 0 C560 0 629 60 629 60 L629 834 L260 834 C150 760 40 620 40 420 Z" fill="var(--teal-deep)"/>
  </svg>

  <div class="cover__photo" role="img" aria-label="Profil eines Roboterkopfes mit technischen Bauteilen vor weißem Grund"></div>

  <p class="brand">VEKTA</p>

  <h1 class="title" aria-label="KI nullzweidrei">
    <span class="title__line title__line--ki">KI</span>
    <span class="title__line title__line--1">NULL</span>
    <span class="title__line title__line--2">ZWEI</span>
    <span class="title__line title__line--3">DREI</span>
  </h1>
</main>
</body>
</html>
```